IT Company requires new Business Card design.

Over the years we have had a few different business card designs. We are now due for new cards across the board for all staff. We felt this would be a good time to start fresh with a new design. Our traditional card simply had our details on the front, and a list of services on the back. We don't particularly need the list of services, we have had cards where the only thing on the rear of the card was our logo.
Feel free to be creative, we would like our tag line "Complete IT Management" to appear at some point, doesn't necessarily have to be with the logo.
I have attached samples and drafts of various previous cards we have used over the years.

```html
<!DOCTYPE html>
<html lang="en">
<head>
<meta charset="UTF-8">
<title>Harbourlink IT – Business Card</title>
<link href="https://fonts.googleapis.com/css2?family=Source+Sans+3:wght@400;600;700&display=swap" rel="stylesheet">
<style>
  :root {
    --slate: #5e6f7e;
    --slate-dark: #4e5d6a;
    --ink: #3f4a54;
    --paper: #ffffff;
    --backdrop: #e9ebee;
    --rule: #c9cfd5;
  }
  * { box-sizing: border-box; margin: 0; padding: 0; }
  html, body { width: 1200px; height: 720px; overflow: hidden; }
  body {
    background: var(--backdrop);
    font-family: "Source Sans 3", sans-serif;
    color: var(--ink);
    position: relative;
  }
  .card {
    position: absolute;
    top: 205px;
    width: 540px;
    height: 310px;
    background: var(--paper);
    box-shadow: 0 2px 8px rgba(0,0,0,0.12);
    overflow: hidden;
  }
  .card--details { left: 40px; }
  .card--brand { left: 620px; }

  /* Details side */
  .top-rule {
    position: absolute; left: 0; right: 0; top: 26px;
    height: 2px; background: var(--slate);
  }
  .name-band {
    position: absolute; left: 0; right: 0; top: 34px; height: 36px;
    background: var(--slate);
    color: var(--paper);
    display: flex; align-items: center; justify-content: center;
    font-size: 17px; letter-spacing: 0.5px;
  }
  .name-band .person { font-weight: 700; text-transform: uppercase; }
  .name-band .role { font-weight: 400; font-size: 13px; text-transform: uppercase; margin-left: 6px; }

  .wordmark-small {
    position: absolute; left: 36px; top: 150px; width: 210px;
    display: flex; align-items: center; gap: 10px;
    color: var(--slate); font-weight: 700; font-size: 28px; letter-spacing: 0.5px;
  }
  .wordmark-small .mark-square { width: 18px; height: 18px; background: var(--slate); flex: none; }

  .divider {
    position: absolute; left: 270px; top: 96px; width: 1px; height: 150px;
    background: var(--rule);
  }
  .contact-list {
    position: absolute; left: 288px; top: 96px;
    list-style: none; font-size: 15px; line-height: 21px; color: var(--ink);
  }
  .contact-list li { display: flex; align-items: center; gap: 8px; }
  .contact-list svg { width: 13px; height: 13px; flex: none; }
  .address {
    position: absolute; left: 288px; top: 212px;
    font-size: 15px; line-height: 19px; color: var(--ink);
  }

  /* Brand side */
  .brand-lockup {
    position: absolute; left: 70px; top: 100px;
    display: flex; align-items: center; gap: 16px;
  }
  .brand-lockup .mark-square { width: 40px; height: 40px; background: var(--slate); }
  .brand-name {
    color: var(--slate); font-weight: 700; font-size: 50px;
    line-height: 1; letter-spacing: 1px; text-transform: uppercase;
  }
  .tagline {
    position: absolute; left: 126px; top: 156px;
    color: var(--slate); font-weight: 600; font-size: 14px;
    letter-spacing: 3.2px; text-transform: uppercase;
  }
  .web-address {
    position: absolute; right: 40px; bottom: 32px;
    color: var(--ink); font-weight: 600; font-size: 19px; letter-spacing: 1.5px;
  }
</style>
</head>
<body>

  <section class="card card--details">
    <div class="top-rule"></div>
    <div class="name-band"><span class="person">Marcus Hale,</span><span class="role">Operation Manager</span></div>

    <div class="wordmark-small"><span class="mark-square"></span><span>HARBOURLINK</span></div>

    <div class="divider"></div>

    <ul class="contact-list">
      <li>
        <svg viewBox="0 0 16 16" aria-hidden="true"><circle cx="8" cy="8" r="7.5" fill="none" stroke="#5e6f7e"/><path d="M5 4.5l1.5-.5 1 2-1 .8a5 5 0 0 0 2.7 2.7l.8-1 2 1-.5 1.5c-3.5.3-6.8-3-6.5-6.5z" fill="#5e6f7e"/></svg>
        08 5550 1234
      </li>
      <li>
        <svg viewBox="0 0 16 16" aria-hidden="true"><rect x="4.5" y="1" width="7" height="14" rx="1.5" fill="#5e6f7e"/><rect x="6" y="3" width="4" height="7" fill="#fff"/></svg>
        0400 555 018
      </li>
      <li>
        <svg viewBox="0 0 16 16" aria-hidden="true"><rect x="4" y="1.5" width="8" height="5" fill="none" stroke="#5e6f7e"/><rect x="1.5" y="6" width="13" height="6" rx="1" fill="#5e6f7e"/><rect x="4" y="10" width="8" height="4.5" fill="#fff" stroke="#5e6f7e"/></svg>
        08 5550 1235
      </li>
      <li>
        <svg viewBox="0 0 16 16" aria-hidden="true"><rect x="1" y="3" width="14" height="10" rx="1" fill="#5e6f7e"/><path d="M1.5 3.5L8 9l6.5-5.5" fill="none" stroke="#fff"/></svg>
        marcus@harbourlinkit.com.au
      </li>
      <li>
        <svg viewBox="0 0 16 16" aria-hidden="true"><circle cx="8" cy="8" r="7" fill="none" stroke="#5e6f7e"/><ellipse cx="8" cy="8" rx="3" ry="7" fill="none" stroke="#5e6f7e"/><path d="M1 8h14" stroke="#5e6f7e"/></svg>
        www.harbourlinkit.com.au
      </li>
    </ul>

    <p class="address">Unit 4 12 Ridgeview Way<br>Riverton WA 6150</p>
  </section>

  <section class="card card--brand">
    <div class="brand-lockup">
      <span class="mark-square"></span>
      <span class="brand-name">Harbourlink IT</span>
    </div>
    <p class="tagline">Complete IT Management</p>
    <p class="web-address">www.harbourlinkit.com.au</p>
  </section>

</body>
</html>
```